Stationery Design Project

Hi All,

We need you to design stationary for a new Business and Accounting Advisory Firm. We have already got the logo designed and it is attached. If you could also if possible, match the fonts in your design to that on the logo’s provided.

What we need:
- Business Card
- A4 Letter head
- A4 Folders
- PPT template (Title page and regular page)

And what ever else you want to throw in.

We are in the process of getting the web site designed, however below is a list of websites which we like which will give you an understanding of the style that we are going for.

- plivant.example
- moldrabay.example
- tarvenhook.example
- quillorbank.example

I look forward to your seeing your design.
Updates

Hi All,

I have just realised that I forgot that i need to include a Sworn Ledgerkeepers image on the letter head, please find attaced as File 1. Could you please have this image in the bottom left header.

Regards,

Marcus

Industry/Entity Type

Business

Requirements
Must have
• Outputs:
- Documents ready to print
- Generic editable information
- Pdf copies of the documents
- Word version of letterhead

```html
<!DOCTYPE html>
<html lang="en">
<head>
<meta charset="utf-8">
<title>Brindlow Partners – Stationery Suite</title>
<link rel="stylesheet" href="https://fonts.googleapis.com/css2?family=Open+Sans:wght@400;600;700;800&display=swap">
<style>
:root{
  --board:#a6a8ab;
  --paper:#ffffff;
  --blue:#2d59a6;
  --cyan:#3aa6d8;
  --orange:#f7941d;
  --orange-deep:#f26b21;
  --ink:#3a3a3a;
  --grey:#8a8c8f;
  --rule:#c9c9c9;
  --bullet:#c0392b;
  --label:#ffffff;
}
*{box-sizing:border-box;margin:0;padding:0}
html,body{width:1200px;height:420px;overflow:hidden}
body{background:var(--board);font-family:"Open Sans",Arial,sans-serif;color:var(--ink);position:relative}
.piece{position:absolute;background:var(--paper);overflow:hidden}
.label{position:absolute;color:var(--label);font-size:13px;font-weight:400}
.stripe{position:absolute;left:0;right:0;height:4px;background:linear-gradient(90deg,var(--blue),var(--cyan) 93%,var(--orange) 93%)}
.stripe-url{position:absolute;left:0;right:0;text-align:center;font-size:3.6px;color:#fff;line-height:4px;letter-spacing:.3px}

/* brand lockup: name in one colour + one plain circle */
.brand{display:flex;align-items:center;gap:3px}
.brand--center{position:absolute;left:0;right:0;justify-content:center}
.brand-dot{border-radius:50%;background:var(--orange);flex:none}
.brand-text{display:flex;flex-direction:column;line-height:1}
.brand-name{color:var(--blue);font-weight:600;white-space:nowrap}
.brand-tag{color:var(--grey);font-weight:400;letter-spacing:1px;white-space:nowrap}
.brand--xs .brand-dot{width:7px;height:7px}.brand--xs .brand-name{font-size:6px}.brand--xs .brand-tag{font-size:3px}
.brand--sm .brand-dot{width:10px;height:10px}.brand--sm .brand-name{font-size:8.5px}.brand--sm .brand-tag{font-size:4px}
.brand--md .brand-dot{width:14px;height:14px}.brand--md .brand-name{font-size:11px}.brand--md .brand-tag{font-size:5px}
.brand--lg .brand-dot{width:16px;height:16px}.brand--lg .brand-name{font-size:12px}.brand--lg .brand-tag{font-size:5.2px}
.watermark{position:absolute;font-weight:800;color:var(--blue);opacity:.07;white-space:nowrap}
.tiny{font-size:3px;color:var(--grey);line-height:4.5px}

/* folder */
.folder-left{left:19px;top:4px;width:152px;height:261px}
.folder-right{left:173px;top:4px;width:153px;height:261px;background:linear-gradient(180deg,#fff,#f1f1f1)}
.folder-flap{position:absolute;left:0;bottom:0;width:100%;height:42px;background:linear-gradient(90deg,#2a4f9c,#3f7cc2);clip-path:polygon(0 0,88% 0,100% 100%,0 100%);display:flex;align-items:center;justify-content:center}
.folder-flap span{color:#fff;font-weight:700;font-size:13px}
.folder-pocket{position:absolute;left:0;bottom:0;width:100%;height:44px;background:#fff;clip-path:polygon(0 0,100% 0,100% 100%,14% 100%);display:flex;align-items:center;justify-content:center}
.folder-pocket span{color:var(--blue);font-weight:700;font-size:13px;margin-left:12px}

/* letterheads */
.letterhead{top:19px;width:155px;height:216px}
.lh-1{left:342px}.lh-2{left:516px}.lh-3{left:692px}
.seal{position:absolute;border-radius:50%;background:#b32025}
.seal-name{position:absolute;font-size:4.2px;font-weight:700;color:var(--ink);line-height:5px}
.contact-col{position:absolute;font-size:2.8px;color:var(--grey);line-height:4px}
.fax-title{position:absolute;left:8px;top:52px;font-size:11px;font-weight:400;color:#222}
.fax-row{position:absolute;left:8px;right:8px;height:7px;font-size:2.8px;color:var(--grey);border-bottom:.5px solid var(--rule);display:flex;justify-content:space-between}
.fax-row span:last-child{width:48%}
.fax-checks{position:absolute;left:8px;right:6px;top:116px;display:flex;justify-content:space-between;font-size:2.8px;color:var(--ink)}
.fax-checks span::before{content:"";display:inline-block;width:4px;height:4px;border:.5px solid #555;margin-right:2px;vertical-align:middle}

/* envelopes */
.env-back{left:947px;top:32px;width:177px;height:79px;background:#f5f5f5}
.env-back-flap{position:absolute;left:0;top:0;width:100%;height:30px;background:linear-gradient(180deg,var(--orange-deep),var(--orange));clip-path:polygon(0 0,100% 0,93% 100%,7% 100%);display:flex;align-items:center;justify-content:center;color:#fff;font-size:8px;font-weight:700}
.env-front{left:927px;top:82px;width:178px;height:98px;background:#fff;box-shadow:0 0 0 .5px #ddd}
.env-mid{left:908px;top:66px;width:197px;height:70px;background:transparent;overflow:visible}

/* business cards */
.card{height:28px;width:84px}
.card-a{left:853px;top:191px}.card-b{left:853px;top:226px}
.card-c{left:943px;top:199px;width:81px;height:45px}
.card-d{left:1027px;top:199px;width:81px;height:45px}
.card-e{left:1111px;top:199px;width:81px;height:45px;background:linear-gradient(135deg,var(--orange),var(--orange-deep));display:flex;align-items:center;justify-content:center}
.card-e span{color:#fff;font-weight:700;font-size:9px}
.card-caption{position:absolute;font-size:3px;color:#fff}

/* slides */
.slide{top:268px;width:161px;height:120px}
.s1{left:164px}.s2{left:333px}.s3{left:507px}.s4{left:679px}.s5{left:851px}.s6{left:1019px}
.slide-title{position:absolute;left:16px;top:7px;font-size:7px;font-weight:800;color:var(--ink)}
.s2 .slide-title,.s3 .slide-title{left:0;right:0;text-align:center}
.slide-body{position:absolute;font-size:2.8px;color:var(--grey);line-height:3.8px}
.photo{position:absolute;top:51px;height:57px;width:71px}
.flow-head{position:absolute;width:24px;height:9px;border-radius:2px;background:linear-gradient(180deg,#5b8fd0,var(--blue));color:#fff;font-size:2.6px;text-align:center;line-height:9px}
.flow-cell{position:absolute;width:19px;height:12px;border-radius:3px/2px;background:linear-gradient(180deg,#fbb040,var(--orange));color:#fff;font-size:2.4px;text-align:center;line-height:12px}
.bullets{position:absolute;list-style:none;font-size:2.9px;color:var(--ink);font-weight:600}
.bullets li{margin-bottom:7.2px}
.bullets li::before{content:"";display:inline-block;width:2.5px;height:2.5px;background:var(--bullet);transform:rotate(45deg);margin-right:3px}
.sub h4{font-size:3.2px;font-weight:700;color:var(--ink)}
.sub h4::before{content:"";display:inline-block;width:2.5px;height:2.5px;background:var(--bullet);transform:rotate(45deg);margin-right:2px}
.sub p{font-size:2.5px;color:var(--grey);line-height:3.3px;margin-left:5px;margin-bottom:5px}
.thanks{position:absolute;left:0;right:0;text-align:center}
</style>
</head>
<body>

<!-- Folder -->
<section class="piece folder-left">
  <div class="watermark" style="left:8px;top:55px;font-size:22px">Brindlow</div>
  <div class="brand brand--md" style="position:absolute;left:30px;top:183px">
    <span class="brand-dot"></span><span class="brand-text"><span class="brand-name">Brindlow Partners</span></span>
  </div>
  <p class="tiny" style="position:absolute;left:16px;top:205px;width:125px">P: (02) 5550 1420 &nbsp; F: (02) 5550 1421 &nbsp; E: info@brindlowpartners.example &nbsp; W: brindlowpartners.example<br>Street Name, City Name, State, City Zip Code</p>
  <div class="folder-flap"><span>Brindlow</span></div>
</section>
<section class="piece folder-right">
  <div class="brand brand--lg brand--center" style="top:66px">
    <span class="brand-dot"></span><span class="brand-text"><span class="brand-name">Brindlow Partners</span><span class="brand-tag">Business Advisors</span></span>
  </div>
  <div class="stripe" style="top:209px;height:5px"></div>
  <div class="stripe-url" style="top:209px">www.brindlowpartners.example</div>
  <div class="folder-pocket"><span>Brindlow</span></div>
</section>
<p class="label" style="left:64px;top:266px">Folder</p>

<!-- Letterhead option 1 -->
<section class="piece letterhead lh-1">
  <div class="brand brand--sm brand--center" style="top:12px">
    <span class="brand-dot"></span><span class="brand-text"><span class="brand-name">Brindlow Partners</span><span class="brand-tag">Business Advisors</span></span>
  </div>
  <div class="watermark" style="left:32px;top:95px;font-size:18px">Brindlow</div>
  <span class="seal" style="left:4px;top:197px;width:14px;height:14px"></span>
  <p class="tiny" style="position:absolute;left:32px;top:202px;font-size:2.6px">Street Name, City Name, State, Zip &nbsp; P: (02) 5550 1420 &nbsp; E: info@brindlowpartners.example &nbsp; www.brindlowpartners.example</p>
</section>
<p class="label" style="left:390px;top:238px">Option-1</p>

<!-- Letterhead option 2 -->
<section class="piece letterhead lh-2">
  <div class="brand brand--sm" style="position:absolute;left:4px;top:6px">
    <span class="brand-dot"></span><span class="brand-text"><span class="brand-name">Brindlow Partners</span><span class="brand-tag">Business Advisors</span></span>
  </div>
  <p class="contact-col" style="left:110px;top:8px;border-left:.5px solid var(--rule);padding-left:3px">P: (02) 5550 1420<br>F: (02) 5550 1421<br>W: brindlowpartners.example</p>
  <span class="seal" style="left:3px;top:190px;width:13px;height:13px"></span>
  <p class="seal-name" style="left:19px;top:191px">Sworn<br>Ledgerkeepers</p>
  <div class="stripe" style="top:206px;height:5px"></div>
  <div class="stripe-url" style="top:206px;font-size:2.8px">Street Name, City Name, State, City Zip Code</div>
</section>
<p class="label" style="left:566px;top:238px">Option-2</p>

<!-- Letterhead option 3 – fax -->
<section class="piece letterhead lh-3">
  <div class="brand brand--sm" style="position:absolute;left:8px;top:7px">
    <span class="brand-dot"></span><span class="brand-text"><span class="brand-name">Brindlow Partners</span><span class="brand-tag">Business Advisors</span></span>
  </div>
  <p class="contact-col" style="left:112px;top:9px;border-left:.5px solid var(--rule);padding-left:3px">Street Name<br>City Name<br>State, Zip</p>
  <p class="fax-title">FAX</p>
  <div class="fax-row" style="top:71px"><span>To:</span><span>From:</span></div>
  <div class="fax-row" style="top:80px"><span>Fax:</span><span>Pages:</span></div>
  <div class="fax-row" style="top:89px"><span>Phone:</span><span>Date:</span></div>
  <div class="fax-row" style="top:98px"><span>Re:</span><span>CC:</span></div>
  <div class="fax-checks"><span>Urgent</span><span>For Review</span><span>Please Comment</span><span>Please Reply</span><span>Please Recycle</span></div>
  <div class="stripe" style="top:208px;height:5px"></div>
  <div class="stripe-url" style="top:208px;font-size:2.8px">P: (02) 5550 1420 • F: (02) 5550 1421 • info@brindlowpartners.example</div>
</section>
<p class="label" style="left:742px;top:238px">Option-3</p>

<!-- Envelopes -->
<section class="piece env-back"><div class="env-back-flap">Brindlow</div></section>
<section class="piece env-front">
  <div class="brand brand--sm" style="position:absolute;left:6px;top:40px">
    <span class="brand-dot"></span><span class="brand-text"><span class="brand-name">Brindlow Partners</span><span class="brand-tag">Business Advisors</span></span>
  </div>
  <p class="tiny" style="position:absolute;left:6px;top:60px">Street Name, City Name, State, City Zip Code</p>
  <div class="stripe" style="top:89px;height:4px"></div>
</section>
<svg class="piece env-mid" viewBox="0 0 197 70" aria-hidden="true">
  <path d="M0 .5H196.5M0 .5L98 46L196.5 .5" fill="none" stroke="#9a9a9a" stroke-width=".6"/>
  <path d="M0 .5L98 46L196.5 .5Z" fill="#fff"/>
  <circle cx="98" cy="28" r="5" fill="var(--orange)"/>
</svg>

<!-- Business cards -->
<section class="piece card card-a">
  <div class="brand brand--xs" style="position:absolute;left:3px;top:9px"><span class="brand-dot"></span><span class="brand-text"><span class="brand-name">Brindlow Partners</span></span></div>
  <p class="tiny" style="position:absolute;left:58px;top:6px;font-size:2.4px;line-height:3.4px">P: 5550 1420<br>F: 5550 1421<br>E: info@bp.example</p>
  <div class="stripe" style="top:23px;height:2px"></div>
</section>
<p class="card-caption" style="left:880px;top:220px">Email Signature - 1</p>
<section class="piece card card-b">
  <div class="brand brand--xs" style="position:absolute;left:14px;top:4px"><span class="brand-dot"></span><span class="brand-text"><span class="brand-name">Brindlow Partners</span></span></div>
  <p class="tiny" style="position:absolute;left:4px;top:14px;font-size:2.4px;line-height:3.4px">Name Here &nbsp; P: 5550 1420<br>Role &nbsp; E: info@bp.example</p>
  <div class="stripe" style="top:24px;height:2px"></div>
</section>
<p class="card-caption" style="left:880px;top:255px">Email Signature - 2</p>
<section class="piece card card-c">
  <div class="brand brand--xs" style="position:absolute;left:14px;top:5px"><span class="brand-dot"></span><span class="brand-text"><span class="brand-name">Brindlow Partners</span></span></div>
  <p class="tiny" style="position:absolute;left:14px;top:16px;font-size:2.6px;line-height:3.6px"><b style="color:var(--ink)">Your Name</b><br>Designation<br>P: (02) 5550 1420<br>E: name@bp.example</p>
  <div class="stripe" style="top:39px;height:3px"></div>
</section>
<section class="piece card card-d">
  <div class="brand brand--xs brand--center" style="top:17px"><span class="brand-dot"></span><span class="brand-text"><span class="brand-name">Brindlow Partners</span></span></div>
  <div class="stripe" style="top:39px;height:3px"></div>
</section>
<section class="piece card card-e"><span>Brindlow</span></section>

<!-- PowerPoint slides -->
<section class="piece slide s1">
  <div class="brand brand--lg brand--center" style="top:30px">
    <span class="brand-dot"></span><span class="brand-text"><span class="brand-name">Brindlow Partners</span><span class="brand-tag">Business Advisors</span></span>
  </div>
  <p style="position:absolute;left:0;right:0;top:70px;text-align:center;font-size:8px;font-weight:700">TITLE OF PRESENTATION</p>
  <div class="stripe" style="top:110px;height:4px"></div>
</section>

<section class="piece slide s2">
  <h3 class="slide-title">LOREM IPSUM</h3>
  <p class="slide-body" style="left:15px;right:15px;top:20px">Lorem ipsum dolor sit amet, consectetuer adipiscing elit, sed diam nonummy nibh euismod tincidunt ut laoreet dolore magna aliquam erat volutpat. Ut wisi enim ad minim veniam, quis nostrud exerci tation ullamcorper suscipit lobortis nisl ut aliquip ex ea commodo consequat.</p>
  <div class="photo" role="img" aria-label="Photo of business people shaking hands in an office" style="left:8px;background:linear-gradient(160deg,#c9d3dc,#5d6873)"></div>
  <div class="photo" role="img" aria-label="Photo of hands reviewing financial documents at a desk" style="left:81px;background:linear-gradient(160deg,#8a8f95,#2e3338)"></div>
</section>

<section class="piece slide s3">
  <h3 class="slide-title">LOREM IPSUM</h3>
  <div class="flow-head" style="left:22px;top:29px">Lorem Ipsum</div>
  <div class="flow-head" style="left:50px;top:29px">Lorem Ipsum</div>
  <div class="flow-head" style="left:78px;top:29px">Lorem Ipsum</div>
  <div class="flow-head" style="left:106px;top:29px">Lorem Ipsum</div>
  <div class="flow-cell" style="left:25px;top:45px">Lorem</div><div class="flow-cell" style="left:53px;top:45px">Lorem</div><div class="flow-cell" style="left:81px;top:45px">Lorem</div><div class="flow-cell" style="left:109px;top:45px">Lorem</div>
  <div class="flow-cell" style="left:25px;top:63px">Lorem</div><div class="flow-cell" style="left:53px;top:63px">Lorem</div><div class="flow-cell" style="left:81px;top:63px">Lorem</div><div class="flow-cell" style="left:109px;top:63px">Lorem</div>
  <div class="flow-cell" style="left:25px;top:81px">Lorem</div><div class="flow-cell" style="left:53px;top:81px">Lorem</div><div class="flow-cell" style="left:81px;top:81px">Lorem</div><div class="flow-cell" style="left:109px;top:81px">Lorem</div>
  <div class="stripe" style="top:111px;height:4px"></div>
</section>

<section class="piece slide s4">
  <h3 class="slide-title">LOREM IPSUM</h3>
  <div class="watermark" style="left:60px;top:30px;font-size:14px;opacity:.05">Brindlow</div>
  <ul class="bullets" style="left:16px;top:34px">
    <li>Lorem ipsum dolor sit amet, consectetuer adipiscing elit, sed diam nonummy.</li>
    <li>Lorem ipsum dolor sit amet, consectetuer adipiscing elit, sed diam nonummy.</li>
    <li>Lorem ipsum dolor sit amet, consectetuer adipiscing elit, sed diam nonummy.</li>
    <li>Lorem ipsum dolor sit amet, consectetuer adipiscing elit, sed diam nonummy.</li>
    <li>Lorem ipsum dolor sit amet, consectetuer adipiscing elit, sed diam nonummy.</li>
    <li>Lorem ipsum dolor sit amet, consectetuer.</li>
  </ul>
  <div class="stripe" style="top:111px;height:4px"></div>
</section>

<section class="piece slide s5">
  <h3 class="slide-title">LOREM IPSUM</h3>
  <div class="watermark" style="left:44px;top:40px;font-size:16px;opacity:.04">Brindlow</div>
  <div class="sub" style="position:absolute;left:14px;top:30px;width:62px">
    <h4>Sub Title 1</h4><p>Lorem ipsum dolor sit amet, consectetuer adipiscing elit, sed diam.</p>
    <h4>Sub Title 2</h4><p>Lorem ipsum dolor sit amet, consectetuer adipiscing elit, sed diam.</p>
    <h4>Sub Title 3</h4><p>Lorem ipsum dolor sit amet, consectetuer adipiscing elit, sed diam.</p>
  </div>
  <div class="sub" style="position:absolute;left:86px;top:30px;width:62px">
    <h4>Sub Title 1</h4><p>Lorem ipsum dolor sit amet, consectetuer adipiscing elit, sed diam.</p>
    <h4>Sub Title 2</h4><p>Lorem ipsum dolor sit amet, consectetuer adipiscing elit, sed diam.</p>
    <h4>Sub Title 3</h4><p>Lorem ipsum dolor sit amet, consectetuer adipiscing elit, sed diam.</p>
  </div>
  <span style="position:absolute;left:138px;top:95px;width:9px;height:9px;border-radius:50%;background:var(--orange);opacity:.5"></span>
  <div class="stripe" style="top:111px;height:4px"></div>
</section>

<section class="piece slide s6">
  <div class="brand brand--lg brand--center" style="top:24px">
    <span class="brand-dot"></span><span class="brand-text"><span class="brand-name">Brindlow Partners</span><span class="brand-tag">Business Advisors</span></span>
  </div>
  <p class="thanks" style="top:55px;font-size:11px;font-weight:800;color:var(--blue)">Thank You!</p>
  <p class="thanks" style="top:72px;font-size:6px;font-weight:700">For your attention</p>
  <p class="thanks" style="top:84px;font-size:3.4px;font-weight:700">www.brindlowpartners.example</p>
</section>
<p class="label" style="left:512px;top:394px">PowerPoint Presentation</p>

</body>
</html>
```